Bref créative
ZARVEN Skin Care
Bright & Fun-filled
Maribel Dunstan
Owner
none on card
zarvenbodycare@plumtree-mail.com
www.zarvenbodycare-shop.com
Natural Skin Care Solutions

```html
<!DOCTYPE html>
<html lang="en">
<head>
<meta charset="utf-8">
<title>ZARVEN Skin Care – Business Card</title>
<link href="https://fonts.googleapis.com/css2?family=Open+Sans:wght@400;600;700&display=swap" rel="stylesheet">
<style>
  :root {
    --backdrop: #ececea;
    --card: #ffffff;
    --leaf-green: #5f8f1f;
    --leaf-light: #a6cf3a;
    --silver: #8c8f93;
    --ink: #3a3a3a;
  }
  html, body {
    margin: 0;
    padding: 0;
    width: 1200px;
    height: 965px;
    overflow: hidden;
    background: var(--backdrop);
    font-family: "Open Sans", Arial, sans-serif;
  }
  .business-card {
    position: absolute;
    left: 240px;
    top: 235px;
    width: 774px;
    height: 440px;
    background: var(--card);
    border-radius: 30px;
    overflow: hidden;
    box-shadow: 0 6px 18px rgba(0, 0, 0, 0.18);
  }
  .edge-swoosh {
    position: absolute;
    inset: 0;
  }
  .brand-name {
    position: absolute;
    left: 0;
    width: 740px;
    top: 92px;
    text-align: center;
    font-size: 82px;
    font-weight: 400;
    letter-spacing: 4px;
    color: var(--silver);
    line-height: 1;
  }
  .brand-band {
    position: absolute;
    left: 199px;
    top: 226px;
    display: flex;
    gap: 4px;
  }
  .brand-band span {
    display: block;
    width: 65px;
    height: 12px;
    border-radius: 2px;
    background: linear-gradient(to bottom, var(--leaf-light), var(--leaf-green));
  }
  .brand-tagline {
    position: absolute;
    left: 199px;
    width: 341px;
    top: 246px;
    margin: 0;
    text-align: center;
    font-size: 13px;
    letter-spacing: 1.5px;
    color: var(--silver);
  }
  .holder {
    position: absolute;
    right: 462px;
    top: 298px;
    text-align: right;
  }
  .holder-name {
    margin: 0;
    font-size: 22px;
    font-weight: 600;
    color: var(--leaf-green);
    line-height: 1.2;
  }
  .holder-role {
    margin: 2px 0 0;
    font-size: 15px;
    color: var(--ink);
  }
  .contact-list {
    position: absolute;
    left: 385px;
    top: 300px;
    margin: 0;
    padding: 0;
    list-style: none;
    font-size: 15px;
    line-height: 26px;
    color: var(--ink);
  }
  .contact-label {
    font-weight: 700;
    color: var(--leaf-green);
  }
</style>
</head>
<body>
  <article class="business-card">
    <svg class="edge-swoosh" width="774" height="440" viewBox="0 0 774 440" aria-hidden="true">
      <defs>
        <linearGradient id="swooshGreen" x1="0" y1="0" x2="1" y2="1">
          <stop offset="0" stop-color="#b6d94a"/>
          <stop offset="1" stop-color="#5e9a1c"/>
        </linearGradient>
        <linearGradient id="swooshSilver" x1="0" y1="0" x2="0" y2="1">
          <stop offset="0" stop-color="#d9dadc"/>
          <stop offset="1" stop-color="#8e9094"/>
        </linearGradient>
      </defs>
      <path d="M 632 0 C 702 60, 742 210, 774 430 L 774 410 C 748 210, 718 62, 658 0 Z" fill="url(#swooshSilver)"/>
      <path d="M 658 0 C 718 62, 748 210, 774 410 L 774 0 Z" fill="url(#swooshGreen)"/>
    </svg>

    <div class="brand-name">ZARVEN</div>
    <div class="brand-band" aria-hidden="true">
      <span></span><span></span><span></span><span></span><span></span>
    </div>
    <p class="brand-tagline">Natural Skin Care Solutions</p>

    <div class="holder">
      <p class="holder-name">Maribel Dunstan</p>
      <p class="holder-role">Owner</p>
    </div>

    <ul class="contact-list">
      <li><span class="contact-label">Email</span> : zarvenbodycare@plumtree-mail.com</li>
      <li><span class="contact-label">Web</span> : www.zarvenbodycare-shop.com</li>
    </ul>
  </article>
</body>
</html>
```